Coach Bruno Velasque Life Coach webpage

I am a Triathlon Coach but now I am in the process of opening a "new brand" as a Life Coach therefore I need new image and a new webpage. I live in Mexico city and would like to offer my services to Latinamerican clientes (spanish speaking). My actual website is www.trenquo.mx. My new website should help me to communicate what I do (Life Coaching), how my services are different from others, help gain new clients through one on one sessions, and I also offer a mental training course. I would like to see designs from a ZEN perspective (minimalistic, light and peaceful colors and not strong colors like my current webpage). The final design should communicate a sense of peace, tranquility, accomplishment and accompaniment. I would like to be able to manipulate the information and add-ons such a section were people can buy, subscribe and pay for the courses.

Target Market(s)

Male and female between 35 and 60 years who are going through changes in their life, need to make important decisions (such a divorcing or not, quitting or changing jobs, or not, etc), and or who do not fell happy with their current life.

Industry/Entity Type

Coaching

Coding

Coded - Design and coding required

Number of Pages Required

5+ page

Font styles to use
Sans Serif

Colors

Designer to choose colors to be used in the design.

Requirements
Must have
• 6 sections and one of those sections a place where my clients can buy courses and pay for them there. I would like to be able to change some of the information easily. I would like to see designs from a ZEN perspective (minimalistic, light and peaceful colors and not strong colors like my current webpage). The final design should communicate a sense of peace, tranquility, accomplishment and accompaniment. I would like to be able to manipulate the informati
Should not have
• dark strong colors

```html
<!DOCTYPE html>
<html lang="en">
<head>
<meta charset="utf-8">
<title>Bruno Velasque — Life Coach</title>
<link href="https://fonts.googleapis.com/css2?family=Montserrat:wght@400;500;600&display=swap" rel="stylesheet">
<style>
:root{
  --ink:#1c1c1c;
  --slate:#7f97b5;
  --slate-dark:#6d85a4;
  --rose:#e8b4b4;
  --rose-soft:#fbf0f0;
  --rose-text:#e3a3a3;
  --line:#dfe6ef;
  --white:#ffffff;
}
*{margin:0;padding:0;box-sizing:border-box}
html,body{width:1200px;height:3622px;overflow:hidden;background:var(--white)}
body{font-family:"Montserrat",sans-serif;color:var(--ink);position:relative}
.abs{position:absolute}
.pill{position:absolute;display:flex;align-items:center;justify-content:center;border-radius:30px;font-size:13px;text-transform:uppercase;letter-spacing:.2px}
.pill.outline{border:2px solid var(--rose);color:var(--ink)}
.pill.fill{background:var(--rose);color:var(--ink);font-weight:500}
.heading{position:absolute;font-size:28px;font-weight:500;color:var(--slate);text-transform:uppercase;letter-spacing:.3px}
.heading span{color:var(--rose-text)}
.rule{position:absolute;height:4px;width:50px;background:var(--slate);border-radius:2px}
.logo{left:114px;top:26px;font-size:26px;font-weight:500;letter-spacing:.5px}
.nav{left:0;top:81px;width:1200px;height:43px;background:#8ea3bf}
.nav a{position:absolute;top:0;height:43px;line-height:43px;color:var(--white);font-size:12.5px;text-decoration:none;transform:translateX(-50%);text-transform:uppercase}
.nav a.active{background:var(--rose);color:var(--ink);padding:0 18px}
.hero{left:0;top:124px;width:1200px;height:469px;background:linear-gradient(180deg,#a9c6e0 0%,#cfe0ee 45%,#7fa3bf 62%,#c9d6d8 76%,#d8d2bd 100%)}
.hero-title{left:60px;width:540px;top:195px;text-align:center;font-size:23px;font-weight:600;line-height:44px;text-transform:uppercase}
.hero-text{left:90px;width:480px;top:286px;text-align:center;font-size:13.5px;line-height:35px}
.card{position:absolute;top:508px;width:236px;height:289px;background:var(--white);border:1px solid var(--line);border-radius:4px;text-align:center}
.card.on{background:var(--rose);border-color:var(--rose)}
.card h3{margin-top:92px;font-size:14.5px;font-weight:500;color:var(--slate);line-height:30px;text-transform:uppercase;padding:0 10px}
.card.on h3{color:var(--ink)}
.card p{font-size:13.5px;line-height:35px;margin-top:6px;padding:0 14px}
.card svg.ico{position:absolute;left:88px;top:22px}
.card .go{position:absolute;left:102px;bottom:-16px;width:32px;height:32px;border-radius:50%;background:var(--rose);border:3px solid var(--white);display:flex;align-items:center;justify-content:center}
.card.on .go{background:var(--slate)}
.about-bg{left:0;top:850px;width:1200px;height:576px;background:linear-gradient(90deg,#eef0f3,#f6f6f7 60%,#eceef2)}
.about-text{left:654px;top:990px;width:440px;font-size:14.5px;line-height:34.5px}
.course{position:absolute;top:1598px;width:219px}
.course .img{height:255px;border-radius:110px 110px 0 0}
.course .t{position:absolute;top:272px;left:0;width:170px;font-size:13.5px;line-height:27px;color:var(--slate);text-transform:uppercase}
.course .arr{position:absolute;right:0;top:286px;width:30px;height:30px;border-radius:50%;border:1.5px solid var(--rose);display:flex;align-items:center;justify-content:center}
.articles{left:0;top:2077px;width:1200px;height:755px;background:var(--rose-soft)}
.date{position:absolute;width:80px;color:var(--white);text-align:center;font-weight:500}
.date b{display:block;font-size:29px;font-weight:500;padding-top:12px}
.date i{font-style:normal;font-size:19px}
.a-title{position:absolute;font-size:17px;line-height:33px;color:var(--slate);text-transform:uppercase}
.a-text{position:absolute;font-size:15px;line-height:33.5px}
.faq{position:absolute;left:686px;width:398px;height:46px;border-bottom:1px solid var(--line);font-size:13px;line-height:46px;text-transform:uppercase}
.faq::after{content:"+";position:absolute;right:0;top:15px;width:13px;height:13px;border:1px solid var(--ink);border-radius:50%;font-size:11px;line-height:11px;text-align:center}
.faq.open{color:var(--rose-text);border:none}
.faq.open::after{content:"–";border-color:var(--rose-text)}
.footer{left:0;top:3297px;width:1200px;height:325px;background:var(--rose-soft)}
.contact{position:absolute;top:3346px;text-align:center;transform:translateX(-50%)}
.contact .c{width:48px;height:48px;border-radius:50%;background:var(--slate);margin:0 auto;display:flex;align-items:center;justify-content:center}
.contact .v{margin-top:36px;font-size:14px;white-space:nowrap}
.contact .l{margin-top:17px;font-size:13px;color:var(--slate);text-transform:uppercase}
.foot-nav{left:0;width:1200px;top:3508px;text-align:center;font-size:13px;text-transform:uppercase}
.foot-nav span{margin:0 20px}
.copy{left:0;width:1200px;top:3553px;text-align:center;font-size:13px;text-transform:uppercase}
</style>
</head>
<body>

<header>
  <div class="abs logo">BRUNO VELASQUE</div>
  <div class="pill fill" style="left:615px;top:24px;width:157px;height:34px;font-weight:400">
    <svg width="12" height="12" viewBox="0 0 24 24" style="margin-right:8px"><path d="M6.6 10.8a15 15 0 006.6 6.6l2.2-2.2c.3-.3.7-.4 1-.2 1.1.4 2.3.6 3.6.6.6 0 1 .4 1 1V20c0 .6-.4 1-1 1A17 17 0 013 4c0-.6.4-1 1-1h3.5c.6 0 1 .4 1 1 0 1.3.2 2.5.6 3.6.1.3 0 .7-.2 1z" fill="#1c1c1c"/></svg>+52 55 4021 7730</div>
  <div class="pill outline" style="left:791px;top:24px;width:139px;height:34px">View courses</div>
  <div class="pill outline" style="left:949px;top:24px;width:139px;height:34px">Online store</div>
</header>

<nav class="abs nav">
  <a class="active" style="left:300px">Home</a>
  <a style="left:415px">About me</a>
  <a style="left:543px">Services</a>
  <a style="left:653px">Blog</a>
  <a style="left:751px">FAQ'S</a>
  <a style="left:874px">Contact us</a>
</nav>

<section>
  <div class="abs hero" role="img" aria-label="Photo of a grey-haired woman with arms spread open on a sunny beach by the sea"></div>
  <h1 class="abs hero-title">Guiding you toward balance,<br>clarity, and fulfillment</h1>
  <p class="abs hero-text">Lorem ipsum dolor sit amet, consectetur adipiscing elit, sed do eiusmod tempor incididunt ut labore et dolore magna aliqua enim ad minim veniam.</p>
  <div class="pill fill" style="left:238px;top:407px;width:182px;height:39px;font-weight:400">Join your program</div>

  <div class="card" style="left:113px">
    <svg class="ico" width="60" height="60" viewBox="0 0 60 60" fill="none" stroke="#e8a5a5" stroke-width="1.6"><circle cx="24" cy="24" r="11"/><path d="M20 35h8M21 39h6M24 6v4M8 24h4M12 12l3 3M36 12l-3 3"/><circle cx="38" cy="38" r="9"/><path d="M45 45l9 9"/></svg>
    <h3>Enhanced clarity &amp; focus</h3>
    <p>Lorem ipsum dolor sit amet, consectetur adipiscing elit, sed eiusmod</p>
    <div class="go"><svg width="10" height="10" viewBox="0 0 10 10"><path d="M3 1l4 4-4 4" stroke="#fff" stroke-width="1.8" fill="none"/></svg></div>
  </div>
  <div class="card on" style="left:359px">
    <svg class="ico" width="60" height="60" viewBox="0 0 60 60" fill="none" stroke="#1c1c1c" stroke-width="1.6"><path d="M18 56V44c-6-4-9-10-8-18 2-10 10-16 20-15 10 1 17 9 16 19l4 8h-5v6c0 3-2 5-5 5h-5v7"/><circle cx="29" cy="29" r="7"/><path d="M29 18v4M29 36v4M18 29h4M36 29h4M30 4v6M42 8l-3 4M20 6l2 5"/></svg>
    <h3>Mindful growth &amp; balance</h3>
    <p>Lorem ipsum dolor sit amet, consectetur adipiscing elit, sed eiusmod</p>
    <div class="go"><svg width="10" height="10" viewBox="0 0 10 10"><path d="M3 1l4 4-4 4" stroke="#fff" stroke-width="1.8" fill="none"/></svg></div>
  </div>
  <div class="card" style="left:605px">
    <svg class="ico" width="60" height="60" viewBox="0 0 60 60" fill="none" stroke="#e8a5a5" stroke-width="1.6"><circle cx="30" cy="28" r="8"/><path d="M16 56c0-10 6-16 14-16s14 6 14 16"/><circle cx="13" cy="12" r="6"/><circle cx="47" cy="12" r="6"/><circle cx="30" cy="8" r="5"/></svg>
    <h3>Emotional resilience</h3>
    <p>Lorem ipsum dolor sit amet, consectetur adipiscing elit, sed eiusmod tempor incididunt</p>
    <div class="go"><svg width="10" height="10" viewBox="0 0 10 10"><path d="M3 1l4 4-4 4" stroke="#fff" stroke-width="1.8" fill="none"/></svg></div>
  </div>
  <div class="card" style="left:851px">
    <svg class="ico" width="60" height="60" viewBox="0 0 60 60" fill="none" stroke="#e8a5a5" stroke-width="1.6"><circle cx="30" cy="22" r="6"/><path d="M20 56V38c0-5 4-8 10-8s10 3 10 8v18M8 56V42M14 56V36M46 56V36M52 56V30M30 2v10M26 6l4-4 4 4"/></svg>
    <h3>Personal empowerment</h3>
    <p>Lorem ipsum dolor sit amet, consectetur adipiscing elit, sed eiusmod tempor incididunt</p>
    <div class="go"><svg width="10" height="10" viewBox="0 0 10 10"><path d="M3 1l4 4-4 4" stroke="#fff" stroke-width="1.8" fill="none"/></svg></div>
  </div>
</section>

<section>
  <div class="abs about-bg" role="img" aria-label="Faded background photo of a group meditation class"></div>
  <svg class="abs" style="left:112px;top:897px" width="470" height="470" viewBox="0 0 470 470">
    <circle cx="234" cy="234" r="224" fill="none" stroke="#7f97b5" stroke-width="9"/>
    <circle cx="238" cy="230" r="224" fill="none" stroke="#e8b4b4" stroke-width="5"/>
  </svg>
  <div class="abs" role="img" aria-label="Portrait photo of a smiling grey-haired coach holding a folder in front of a whiteboard" style="left:135px;top:918px;width:422px;height:422px;border-radius:50%;background:radial-gradient(circle at 55% 45%,#eceff1 0%,#dfe3e6 55%,#c9ccd0 100%)"></div>
  <h2 class="heading" style="left:654px;top:918px">About <span>me</span></h2>
  <div class="rule" style="left:654px;top:963px"></div>
  <p class="abs about-text">Lorem ipsum dolor sit amet, consectetur adipiscing elit, sed do eiusmod tempor incididunt ut labore et dolore magna aliqua. Ut enim ad minim veniam, quis nostrud exercitation ullamco laboris nisi ut aliquip ex ea commodo consequat.</p>
  <p class="abs about-text" style="top:1135px">Lorem ipsum dolor sit amet, consectetur adipiscing elit, sed do eiusmod tempor incididunt ut labore et dolore magna aliqua. Ut enim ad minim veniam, quis nostrud exercitation ullamco laboris nisi ut aliquip ex ea commodo consequat.</p>
  <div class="pill fill" style="left:654px;top:1291px;width:147px;height:42px;font-size:14px">Learn more</div>
</section>

<section>
  <h2 class="heading" style="left:0;width:1200px;text-align:center;top:1502px">Our <span>courses</span></h2>
  <div class="rule" style="left:567px;top:1549px;width:66px"></div>
  <div class="course" style="left:111px"><div class="img" role="img" aria-label="Photo of women meditating seated in a row on yoga mats" style="background:linear-gradient(180deg,#e9e1d8,#b9a999)"></div><div class="t">Building emotional resilience</div><div class="arr"><svg width="12" height="12" viewBox="0 0 12 12"><path d="M3 9l6-6M4 3h5v5" stroke="#e8a5a5" stroke-width="1.4" fill="none"/></svg></div></div>
  <div class="course" style="left:363px"><div class="img" role="img" aria-label="Photo of an older couple jogging in an autumn park" style="background:linear-gradient(180deg,#b8a850,#6f7c46 60%,#8a8f8e)"></div><div class="t">Developing inner strength</div><div class="arr"><svg width="12" height="12" viewBox="0 0 12 12"><path d="M3 9l6-6M4 3h5v5" stroke="#e8a5a5" stroke-width="1.4" fill="none"/></svg></div></div>
  <div class="course" style="left:616px"><div class="img" role="img" aria-label="Photo of a speaker presenting to a seated audience" style="background:linear-gradient(180deg,#e7ddd3,#a79a8b 65%,#39465a)"></div><div class="t" style="top:286px">Sustainable focus</div><div class="arr"><svg width="12" height="12" viewBox="0 0 12 12"><path d="M3 9l6-6M4 3h5v5" stroke="#e8a5a5" stroke-width="1.4" fill="none"/></svg></div></div>
  <div class="course" style="left:868px"><div class="img" role="img" aria-label="Photo of a man meditating with eyes closed and hands in mudra" style="background:linear-gradient(180deg,#eef0f2,#cfd3d6 60%,#3d4249)"></div><div class="t">Practical mindfulness tools</div><div class="arr"><svg width="12" height="12" viewBox="0 0 12 12"><path d="M3 9l6-6M4 3h5v5" stroke="#e8a5a5" stroke-width="1.4" fill="none"/></svg></div></div>
  <div class="pill fill" style="left:495px;top:1950px;width:210px;height:40px;font-size:14px;font-weight:400">View more courses</div>
</section>

<section>
  <div class="abs articles"></div>
  <h2 class="heading" style="left:116px;top:2138px">Latest <span>articles</span></h2>
  <div class="rule" style="left:116px;top:2184px;width:66px"></div>

  <div class="abs" role="img" aria-label="Photo of a smiling woman in sportswear eating a fruit bowl on the floor" style="left:115px;top:2252px;width:469px;height:270px;border-radius:8px;background:linear-gradient(90deg,#e8ebee,#c9cfc8 55%,#8ea07a)"></div>
  <div class="date" style="left:134px;top:2502px;height:88px;background:var(--slate)"><b>04</b><i>FEB</i></div>
  <div class="a-title" style="left:240px;top:2534px">Lorem ipsum dolor sit amet,<br>consectetur</div>
  <p class="a-text" style="left:134px;top:2608px;width:440px">Lorem ipsum dolor sit amet, consectetur adipiscing elit, sed do eiusmod tempor incididunt ut labore et dolore magna aliqua.</p>

  <div class="abs" role="img" aria-label="Photo of a group of adults doing neck stretches in a bright studio" style="left:611px;top:2140px;width:469px;height:271px;border-radius:8px;background:linear-gradient(90deg,#dfe3e4,#c6c9c5 50%,#8b9aa2)"></div>
  <div class="date" style="left:629px;top:2391px;height:82px;background:#bdb9b6"><b>18</b><i>JAN</i></div>
  <div class="a-title" style="left:736px;top:2422px">Lorem ipsum dolor sit amet,<br>consectetur</div>
  <p class="a-text" style="left:629px;top:2496px;width:450px">Lorem ipsum dolor sit amet, consectetur adipiscing elit, sed do eiusmod tempor incididunt ut labore et dolore magna aliqua. Ut enim ad minim veniam, quis nostrud exercitation ullamco laboris nisi ut aliquip ex ea commodo consequat&nbsp; aute irure dolor in reprehenderit in voluptate velit esse cillum.</p>

  <div class="pill fill" style="left:495px;top:2727px;width:210px;height:40px;font-size:14px;font-weight:400">View more articles</div>
</section>

<section>
  <h2 class="heading" style="left:110px;top:2912px;font-size:25px;line-height:46px">Sign up for&nbsp; Bruno Velasque<br>with a <span>discount offer</span></h2>
  <div class="rule" style="left:111px;top:3020px;width:66px"></div>
  <div class="abs" style="left:111px;top:3065px;width:448px;height:47px;background:var(--white);box-shadow:0 2px 8px rgba(0,0,0,.08);font-size:13px;line-height:47px;padding-left:17px;color:#8a8f96">ENTER EMAIL ADDRESS</div>
  <div class="abs" style="left:510px;top:3065px;width:49px;height:47px;background:var(--rose);display:flex;align-items:center;justify-content:center"><svg width="15" height="15" viewBox="0 0 24 24"><path d="M22 2L2 10l8 3 3 8z" fill="#1c1c1c"/></svg></div>

  <h2 class="heading" style="left:686px;top:2914px;font-size:25px">Your questions <span>answered</span></h2>
  <div class="rule" style="left:686px;top:2961px;width:66px"></div>
  <div class="faq" style="top:2983px">What are the benefits of life coaching ?</div>
  <div class="faq" style="top:3029px">How many sessions do I need to see results ?</div>
  <div class="faq" style="top:3075px">Lorem ipsum dolor sit amet, consectetur?</div>
  <div class="faq open" style="top:3121px">Lorem ipsum dolor sit amet, consectetur?</div>
  <p class="abs" style="left:686px;top:3162px;width:400px;font-size:12px;line-height:31px">Lorem ipsum dolor sit amet, consectetur adipiscing elit, sed do eiusmod tempor incididunt ut labore et dolore magna aliqua.</p>
</section>

<footer>
  <div class="abs footer"></div>
  <div class="contact" style="left:221px"><div class="c"><svg width="18" height="18" viewBox="0 0 24 24"><path d="M6.6 10.8a15 15 0 006.6 6.6l2.2-2.2c.3-.3.7-.4 1-.2 1.1.4 2.3.6 3.6.6.6 0 1 .4 1 1V20c0 .6-.4 1-1 1A17 17 0 013 4c0-.6.4-1 1-1h3.5c.6 0 1 .4 1 1 0 1.3.2 2.5.6 3.6.1.3 0 .7-.2 1z" fill="#fff"/></svg></div><div class="v">+52 55 4021 7730</div><div class="l">Our phone</div></div>
  <div class="contact" style="left:495px"><div class="c"><svg width="18" height="18" viewBox="0 0 24 24"><rect x="3" y="6" width="18" height="13" rx="1" fill="#fff"/><path d="M3 7l9 7 9-7" stroke="#7f97b5" stroke-width="1.6" fill="none"/></svg></div><div class="v">HOLA@CALMAVIVA.MX</div><div class="l">Our mail</div></div>
  <div class="contact" style="left:873px"><div class="c"><svg width="18" height="18" viewBox="0 0 24 24"><path d="M12 2a7 7 0 00-7 7c0 5 7 13 7 13s7-8 7-13a7 7 0 00-7-7z" fill="#fff"/><circle cx="12" cy="9" r="2.6" fill="#7f97b5"/></svg></div><div class="v">AV. SERENA NO. 45, PISO 3, COL. ROMA, CDMX</div><div class="l">Our address</div></div>
  <div class="abs foot-nav">Home<span>|</span>About me<span>|</span>Services<span>|</span>Latest blog<span>|</span>FAQ'S<span>|</span>Contact us</div>
  <div class="abs copy">Copyright © 2024 Bruno Velasque. All rights reserved.</div>
</footer>

</body>
</html>
```